Bold Harbor Web Design Layout (no HTML)

We require the layout only for a website.  No html or logo is required - just the layout.

A refreshed and revitalized website to coincide with the relaunch of our brand. We are looking for a clean simplistic design that is easy to use and presents relevant information effectively.
We are an events management company specializing in conferences.
Updates

Thank you for your design. We really like the imagery. Essentially we are after a home page design (one page) that incorporates the 3 main buttons (request a proposal, select a venue and specials) while providing the relevant information on our service via functionality similar to that on www.plivtrak.com ie using the large arrow to scroll over the relevant topic to receive information. We hope to finalise the contest in the next week and hope to consider your revised entry.

Thanks!

Target Market(s)

Australian corporate sector primarily Managing Directors or their assistants. Any business looking to hold a conference for up 500 delegates however we are primarily targeting the decision maker so need to ensure we are communicating on their terms.

Industry/Entity Type

Event

Requirements
Must have
• Incorporate the elements from the attached document however with complete creative license as to their layout. Our main competitors are gathorly.com.au, talkhollowhq.com.au both sites are bland and not user friendly.
Nice to have
• Colours red, silver and black. Note we are running a separate contest to refresh our logo.
• We like the functionality of plivtrak.com

```html
<!DOCTYPE html>
<html lang="en">
<head>
<meta charset="utf-8">
<title>Bold Harbor – Conference Management</title>
<link href="https://fonts.googleapis.com/css2?family=Questrial&family=Arimo:wght@400;700&display=swap" rel="stylesheet">
<style>
:root{
  --red:#c4000b;
  --red-dark:#8e0a12;
  --black:#000;
  --charcoal:#3c3c3c;
  --silver:#c2c2c2;
  --silver-light:#e8e8e8;
  --panel:#e9e9e9;
  --text:#111;
  --muted:#6a6a6a;
  --white:#fff;
}
*{box-sizing:border-box;margin:0;padding:0}
html,body{width:1200px;height:717px;overflow:hidden}
body{
  position:relative;font-family:"Questrial",sans-serif;color:var(--text);
  background:linear-gradient(#000 0,#4a4a4a 55px,#9a9a9a 98px,var(--silver-light) 98px,var(--silver-light) 138px,var(--silver) 138px);
}
.abs{position:absolute}
.page{left:158px;top:9px;width:882px;height:622px;background:var(--white);border-radius:7px;box-shadow:0 0 10px rgba(0,0,0,.35)}
.masthead{left:167px;top:17px;width:865px;height:81px;background:var(--silver);border-radius:6px 6px 0 0}
.logo-slot{left:205px;top:60px;font-family:"Arimo",sans-serif;font-size:10px;letter-spacing:-.2px}
.search-label{left:754px;top:70px;font-family:"Arimo",sans-serif;font-weight:700;font-size:13px}
.search-field{left:815px;top:67px;width:180px;height:20px;background:var(--white);border:1px solid #d5d5d5}
.search-go{left:994px;top:64px;width:28px;height:27px;border-radius:3px;background:linear-gradient(#e0545a,var(--red) 55%,var(--red-dark));color:var(--white);font-family:"Arimo",sans-serif;font-weight:700;font-size:11px;display:flex;align-items:center;justify-content:center;border:1px solid #fff}
.nav{left:167px;top:98px;width:865px;height:40px;background:var(--charcoal);display:flex;gap:11px;padding-left:70px;align-items:center;padding-top:7px}
.nav a{color:var(--white);text-decoration:none;font-size:13px;position:relative}
.nav a.current{color:#cfe0ef;font-weight:700}
.nav a.current::after{content:"";position:absolute;left:50%;bottom:-10px;margin-left:-5px;border:5px solid transparent;border-bottom-color:var(--white)}
.side-menu{left:167px;top:194px;width:134px}
.side-menu li{list-style:none;height:28px;line-height:28px;padding-left:19px;font-size:14px}
.side-menu li.active{color:var(--white);background:linear-gradient(#d5141c,var(--red-dark));clip-path:polygon(0 0,93% 0,100% 50%,93% 100%,0 100%);box-shadow:0 2px 3px rgba(0,0,0,.3)}
.side-rule{left:303px;top:160px;width:1px;height:437px;background:linear-gradient(var(--white),#ccc 15%,#ccc 85%,var(--white))}
.intro{left:329px;top:160px;width:480px;font-size:16px;line-height:19.6px}
.intro b{font-family:"Arimo",sans-serif}
.goal{left:822px;top:167px;width:200px;color:var(--red);font-size:16px;line-height:19px}
.offer{left:314px;top:239px;width:494px;height:237px;background:var(--panel);border-radius:9px}
.offer h2{position:absolute;left:33px;top:10px;font-family:"Arimo",sans-serif;font-size:15px;color:var(--muted)}
.offer ul{position:absolute;left:148px;top:44px;font-size:13px;line-height:15.8px;color:var(--muted);list-style:none}
.offer ul li::before{content:"•";margin-right:8px}
.offer p{position:absolute;left:148px;top:170px;width:330px;font-size:13px;line-height:16px;color:var(--muted)}
.offer .art{position:absolute;left:30px;top:56px;width:100px;height:150px;border-radius:40px;background:radial-gradient(circle at 45% 40%,#f04a3a,#b30e10 60%,rgba(233,233,233,0) 72%)}
.benefits{left:816px;top:239px;width:203px;height:241px;border-radius:8px;background:linear-gradient(90deg,#d2141c,var(--red-dark))}
.benefits li{position:absolute;left:12px;list-style:none;color:var(--white);font-size:20px;line-height:21px}
.pointer{left:764px;top:264px;width:250px;height:56px}
.pointer span{position:absolute;left:64px;top:13px;color:var(--white);font-size:20px}
.promo{top:493px;width:200px;height:100px}
.promo h3{height:18px;background:var(--red);color:var(--white);font-weight:400;font-size:12px;line-height:18px;padding-left:9px;border-radius:0 5px 0 0}
.promo p{position:absolute;left:5px;top:19px;width:110px;font-size:10.5px;line-height:12.5px}
.promo .art{position:absolute;right:12px;top:30px;width:70px;height:70px}
.promo-divider{top:485px;width:1px;height:112px;background:linear-gradient(var(--white),#ccc,var(--white))}
.footer{left:167px;top:598px;width:865px;height:24px;background:var(--black);color:var(--white);font-family:"Arimo",sans-serif;font-size:9px;text-align:center;line-height:24px}
</style>
</head>
<body>
<div class="abs page"></div>
<header>
  <div class="abs masthead"></div>
  <div class="abs logo-slot">LOGO GOES HERE</div>
  <div class="abs search-label">SEARCH:</div>
  <div class="abs search-field"></div>
  <div class="abs search-go">GO</div>
  <nav class="abs nav">
    <a class="current" href="#">HOME</a><a href="#">SERVICES</a><a href="#">VENUES</a><a href="#">CLIENTS</a><a href="#">REGISTER</a><a href="#">CONTACT US</a>
  </nav>
</header>

<ul class="abs side-menu">
  <li class="active">OTHER MENU</li><li>OTHER MENU</li><li>OTHER MENU</li><li>OTHER MENU</li><li>OTHER MENU</li><li>OTHER MENU</li>
</ul>
<div class="abs side-rule"></div>

<p class="abs intro"><b>Bold Harbor</b>’ professional conference team specialises in solutions. We work closely with a core group of clients to ensure desired outcomes, on time and in budget.</p>
<p class="abs goal">Our goal is to make sure your conference is:</p>

<section class="abs offer">
  <h2>We offer a complete range of finance&nbsp; packages including;</h2>
  <div class="art" role="img" aria-label="Large red 3D dollar sign"></div>
  <ul>
    <li>total conference underwriting</li>
    <li>online delegate payment gateway</li>
    <li>substantially discounted rooming rates</li>
    <li>no upfront costs</li>
    <li>zero management fees</li>
    <li>free venue sourcing</li>
    <li>free delegate booking management</li>
  </ul>
  <p>Minimise your costs and free your cash flow to focus on your core business functions. We’ll ensure maximum return from your conference budget.</p>
</section>

<ul class="abs benefits">
  <li style="top:104px">Expertely Managed<br>&amp; Hassle Free</li>
  <li style="top:164px">Outcome Focussed</li>
  <li style="top:206px">Well Attended</li>
</ul>
<div class="abs pointer">
  <svg width="250" height="56" viewBox="0 0 250 56">
    <defs><linearGradient id="pointerFill" x1="0" y1="0" x2="0" y2="1"><stop offset="0" stop-color="#6a6a6a"/><stop offset=".5" stop-color="#2e2e2e"/><stop offset="1" stop-color="#111"/></linearGradient></defs>
    <path d="M2 28 L28 2 H244 a4 4 0 0 1 4 4 V50 a4 4 0 0 1 -4 4 H28 Z" fill="url(#pointerFill)" stroke="#fff" stroke-width="3"/>
  </svg>
  <span>Cost Effective</span>
</div>

<section class="abs promo" style="left:314px">
  <h3>Special Offers</h3>
  <p>Not sure where to start? We have over 60 properties to choose from both domestically and international.</p>
  <div class="art" role="img" aria-label="Red starburst badge with dollar sign" style="border-radius:50%;background:radial-gradient(circle,#e8312a,#a50d10)"></div>
</section>
<div class="abs promo-divider" style="left:541px"></div>
<section class="abs promo" style="left:563px">
  <h3>Request Proposal</h3>
  <p>Not sure where to start? We have over 60 properties to choose from both domestically and international.</p>
  <div class="art" role="img" aria-label="Red-rimmed wall clock" style="border-radius:50%;background:radial-gradient(circle,#fafafa 60%,#c81a1f 64%,#8e0a12)"></div>
</section>
<div class="abs promo-divider" style="left:806px"></div>
<section class="abs promo" style="left:819px">
  <h3>Browse Conference</h3>
  <p>Not sure where to start? We have over 60 properties to choose from both domestically and international.</p>
  <div class="art" role="img" aria-label="Red map of Australia" style="border-radius:30%;background:linear-gradient(135deg,#f0443a,#a50d10)"></div>
</section>

<footer class="abs footer">Ph: 1300 555 274. P.O. Box 4417, Kelbrook NSW 2094. Bold Harbor. All Rights Reserved. 2009</footer>
</body>
</html>
```